E-Book-Cover für einen Kriminalroman
Zielgruppe
Ich veröffentliche meinen Roman “Die Schwelle” als E-Book.
Das Buch spielt in einer nahen Zukunft, in der Die Schwelle Nachrichten in die Vergangenheit möglich macht. Unfälle und Straftaten werden sofort ungeschehen gemacht. Jeder Bürger kann seinem vergangenen Ich eine Botschaft schicken - und so die eigene Geschichte “reparieren”. Auch Henrik, ein unscheinbarer Projektleiter, erhält eines Tag eine Nachricht aus der Zukunft: 'Halte dich von Maren fern. Sie wird dein Untergang sein'. Die Nachricht stellt Henrik vor ein Rätsel. Vor welcher Gefahr hat er sich gewarnt? Und wer ist Maren? Ein Jahr später wird Henrik durch Zufall Mitwisser einer politischen Verschwörung. Die Killer machen Jagd auf ihn und kennen jeden seiner nächsten Schritte. Die letzte Rettung ist ausgerechnet eine Frau namens Maren.
--- “Die Schwelle” spielt in der Zukunft, ist aber kein Science Fiction Roman. Die beschriebene Welt ist (außer der Zeitmanipulation) wie die unsere. Am ehesten ist das Buch also ein actionreicher Kriminalroman.
Die Hauptzielgruppe sind 25 - 45-jährige, zum Beispiel Leser von Rolf Ebenhöch, Tobias Wendrath oder Karl Vossberg.
Aufgabenstellung
Gewünscht ist ein E-Book-Cover für die Verwendung auf Online-Plattformen wie Kaufora.
Autor: K.J. Brandau
Titel: Die Schwelle
Zusatz: Roman
Visuelle Anforderungen
Das Cover sollte eine Reihe von Türen zeigen. Begründung dazu: Im sogenannten Registerbüro muss der Protagonist in einer von vier nebeneinanderliegenden Türen treten und empfängt dort seine Nachricht aus der Zukunft. Das Thema “Entscheidungen fürs Leben” des Romans wird durch diese Türen visualisiert und als Symbol mehrmals aufgegriffen - dementsprechend ist es aus meiner Sicht perfekt für das Cover.
Für die Fotosuche: Das Registerbüro ist leicht heruntergekommen und wirkt kühl und unsympathisch. Dieses Bild https://de.bildquelle-beispiel.de/id/19384726 (auch noch einmal angehängt) zum Beispiel passt sehr gut.
Thema Hacking und Programmieren
Das Buch spielt in den Lebenswelten von Programmierern und Hackern; Die Schwelle ist eine Datenbank. Dies könnte durch Stil der Schrift oder anders unterstützt werden. Nur, wenn sinnvoll und ohne dass es wie ein Computerbuch aus den 90ern wirkt natürlich :)
- Die Font kann das Thema aufgreifen, aber bitte KEINE Vintage LED-Schrift im Stil von http://www.schriftkiste-beispiel.de/segment-alt.font, sondern eine die einem modernen Monitor entspringt. Entweder verpixelt (Beispiel im Anhang) oder durch eine gepunktete Schrift in hoher "Auflösung" (Beispiel: http://www.schriftkiste-beispiel.de/perlen-raster.font, also nicht nur 7 Punkte in der Breite), hier könnte man die Ränder auch etwas blurren, um den Effekt eines Monitors zu erzielen
- Wenn der o.g. Schriftstil benutzt wird, bitte in Kleinbuchstaben (wie ein Befehl auf dem Terminal)
-> All kein Muss, nur wenn sinnvoll!
Weitere Anforderungen:
- Die Türen befinden sich in einem kühlen, sterilen BÜRO, dementsprechend dürfen sie nicht zu hübsch aussehen oder an Wohnzimmertüren erinnern
- Wenn Codezeilen als Hintergrundbestandteil genutzt..

```html
<!DOCTYPE html>
<html lang="de">
<head>
<meta charset="utf-8">
<title>Die Schwelle – Coverentwürfe</title>
<link rel="stylesheet" href="https://fonts.googleapis.com/css2?family=Bebas+Neue&family=Old+Standard+TT:wght@400&family=Open+Sans:wght@400&display=swap">
<style>
  :root {
    --paper: #ffffff;
    --cover-bg: #0b0b0b;
    --ink-light: #ffffff;
    --glow-mid: #8a8a8a;
    --glow-soft: #2c2c2c;
  }
  * { box-sizing: border-box; margin: 0; padding: 0; }
  html, body {
    width: 1200px;
    height: 848px;
    overflow: hidden;
    background: var(--paper);
  }
  .sheet {
    position: relative;
    width: 1200px;
    height: 848px;
  }
  .cover {
    position: absolute;
    top: 109px;
    width: 418px;
    height: 656px;
    background: var(--cover-bg);
    overflow: hidden;
    color: var(--ink-light);
  }
  .cover--condensed { left: 159px; }
  .cover--serif { left: 649px; }

  .cover__scene {
    position: absolute;
    left: 0;
    right: 0;
    top: 250px;
    bottom: 0;
    background:
      radial-gradient(ellipse 30% 38% at 52% 42%, var(--glow-mid) 0%, var(--glow-soft) 50%, rgba(11,11,11,0) 100%),
      radial-gradient(ellipse 45% 14% at 50% 72%, rgba(170,170,170,0.45) 0%, rgba(11,11,11,0) 100%),
      linear-gradient(to bottom, var(--cover-bg) 0%, #1a1a1a 40%, #121212 72%, #000 100%);
  }

  .cover__author {
    position: absolute;
    top: 20px;
    left: 0;
    right: 0;
    text-align: center;
    white-space: nowrap;
    font-family: "Open Sans", sans-serif;
    font-weight: 400;
    font-size: 25px;
    letter-spacing: 0.5em;
    padding-left: 0.5em;
    line-height: 1.2;
  }

  .cover__title-article,
  .cover__title-word {
    position: absolute;
    left: 0;
    right: 0;
    text-align: center;
    white-space: nowrap;
    line-height: 1;
    font-weight: 400;
  }

  .cover--condensed .cover__title {
    font-family: "Bebas Neue", sans-serif;
  }
  .cover--condensed .cover__title-article {
    top: 120px;
    font-size: 36px;
    left: -74px;
  }
  .cover--condensed .cover__title-word {
    top: 143px;
    font-size: 105px;
  }

  .cover--serif .cover__title {
    font-family: "Old Standard TT", serif;
  }
  .cover--serif .cover__title-article {
    top: 104px;
    font-size: 64px;
  }
  .cover--serif .cover__title-word {
    top: 164px;
    font-size: 56px;
  }

  .cover__label {
    position: absolute;
    left: 0;
    right: 0;
    top: 585px;
    text-align: center;
    font-family: "Open Sans", sans-serif;
    font-size: 16px;
    letter-spacing: 0.02em;
    line-height: 1.2;
  }
</style>
</head>
<body>
<main class="sheet">

  <article class="cover cover--condensed">
    <div class="cover__scene" role="img" aria-label="Foto: dunkler Büroflur mit drei Türen, die mittlere steht offen und Licht fällt auf den Boden"></div>
    <p class="cover__author">K.J. BRANDAU</p>
    <h1 class="cover__title">
      <span class="cover__title-article">DIE</span>
      <span class="cover__title-word">SCHWELLE</span>
    </h1>
    <p class="cover__label">ROMAN</p>
  </article>

  <article class="cover cover--serif">
    <div class="cover__scene" role="img" aria-label="Foto: dunkler Büroflur mit drei Türen, die mittlere steht offen und Licht fällt auf den Boden"></div>
    <p class="cover__author">K.J. BRANDAU</p>
    <h1 class="cover__title">
      <span class="cover__title-article">DIE</span>
      <span class="cover__title-word">SCHWELLE</span>
    </h1>
    <p class="cover__label">ROMAN</p>
  </article>

</main>
</body>
</html>
```